Trifold - Brandt Commercial Roofing

Enhance the look, change the images if needed. Create some interest please!

Target Market(s)

Commercial and Industrial Building Owners

Industry/Entity Type

Roofing

Font styles to use
Serif

Requirements
Must have
• Organized layout, call to action

```html
<!DOCTYPE html>
<html lang="en">
<head>
<meta charset="utf-8">
<title>Brandt Commercial Roofing – Trifold</title>
<link rel="stylesheet" href="https://fonts.googleapis.com/css2?family=Montserrat:wght@400;500;600;700;800&display=swap">
<style>
:root{
  --ink:#111111;
  --black:#0d0d0d;
  --orange:#f07a24;
  --grey-box:#ececec;
  --text:#444444;
  --page:#f2f2f2;
  --white:#ffffff;
}
*{box-sizing:border-box;margin:0;padding:0}
html,body{width:1200px;height:2666px;overflow:hidden}
body{background:var(--page);font-family:"Montserrat",sans-serif;color:var(--text);position:relative}
.sprite{display:none}

.spread{position:absolute;left:40px;width:1120px;height:790px;background:var(--white);box-shadow:0 8px 28px rgba(0,0,0,.18);overflow:hidden}
.spread--inside{top:420px}
.spread--outside{top:1460px}

.footer-band{position:absolute;left:0;right:0;bottom:0;height:95px;background:linear-gradient(180deg,#2a2a2a 0%,var(--black) 35%)}
.footer-band .url{position:absolute;bottom:24px;width:373.33px;text-align:center;color:var(--white);font-weight:600;font-size:14px;letter-spacing:2px}

/* inside spread */
.header-band{position:absolute;left:0;right:0;top:0;height:115px;background:var(--black)}
.panel{position:absolute;top:0;width:373.33px;height:695px;padding:28px 22px 0}
.panel--1{left:0}.panel--2{left:373.33px}.panel--3{left:746.66px}
.panel-title{display:flex;align-items:center;gap:14px;height:52px;margin-bottom:12px}
.badge{width:54px;height:54px;border-radius:50%;background:var(--white);border:3px solid var(--orange);display:flex;align-items:center;justify-content:center}
.panel-title h2{color:var(--white);font-weight:700;font-size:27px;letter-spacing:1px}
.card{background:var(--grey-box);padding:3px 3px 12px}
.photo{border-radius:8px;border:3px solid #d6d6d6}
.photo-row{display:flex;gap:6px}
.ticks{list-style:none;display:grid;grid-template-columns:1.35fr 1fr;gap:5px 8px;padding:10px 8px 0}
.ticks li{display:flex;gap:7px;font-size:12px;font-weight:600;color:var(--ink);line-height:1.2}
.ticks--single{grid-template-columns:1fr;gap:5px}
.ticks--single li{font-weight:500}
.ticks--single b{font-weight:700}
.tick{flex:0 0 13px;width:13px;height:13px;margin-top:1px}
.copy{font-size:12.5px;line-height:1.3;color:var(--text);padding:10px 10px 0}
.muted{color:#666}

/* outside spread */
.founder-block{position:absolute;left:0;top:0;width:345px;height:150px;background:var(--black)}
.founder-photo{position:absolute;left:32px;top:40px;width:298px;height:345px;border:4px solid var(--white);background:linear-gradient(160deg,#6b4a35 0%,#c8a27f 45%,#2a1f1c 100%)}
.founder{position:absolute;left:30px;top:400px;width:310px}
.founder h3{font-size:20px;font-weight:600;color:var(--ink)}
.founder .role{color:var(--orange);font-size:13.5px;font-weight:500;line-height:1.2;margin:6px 0 14px}
.founder p{font-size:10.5px;line-height:1.22;color:var(--text)}

.mission{position:absolute;left:395px;top:40px;width:300px}
.mission h3{font-size:25px;font-weight:400;color:var(--ink);line-height:1.05}
.mission h3 strong{font-weight:800;display:block}
.mission p{font-size:12px;line-height:1.25;margin-top:10px;color:var(--text)}
.mission .invite{font-weight:700;color:var(--ink)}
.charity{margin-top:18px}
.charity h4{color:var(--orange);font-size:14px;font-weight:600}
.charity .row{display:flex;gap:10px;margin-top:6px}
.charity svg{flex:0 0 30px}
.charity h5{font-size:14px;font-weight:700;color:var(--ink)}
.charity .row p{margin-top:0;font-size:11.5px}
.contact{position:absolute;left:395px;top:510px;width:290px;text-align:center}
.contact .phone{font-size:24px;font-weight:700;color:var(--ink);margin:4px 0 6px}
.contact .addr{font-size:12.5px;font-weight:600;color:var(--ink);line-height:1.2;margin-top:4px}

.brand{position:absolute;left:790px;top:40px;width:300px;display:flex;align-items:center;justify-content:center;gap:10px}
.brand .mark{width:14px;height:14px;border-radius:50%;background:var(--ink)}
.brand .name{font-size:20px;font-weight:700;color:var(--ink);line-height:1.2}
.diagonal{position:absolute;left:0;top:0}
.values{position:absolute;left:760px;top:520px;width:340px;text-align:center;font-weight:800;font-size:30px;line-height:1.05;color:var(--ink)}
.values .hl{color:var(--orange)}
</style>
</head>
<body>

<svg class="sprite" aria-hidden="true">
  <symbol id="tick" viewBox="0 0 14 14"><circle cx="7" cy="7" r="6" fill="none" stroke="#f07a24" stroke-width="1.3"/><path d="M4 7.2l2 2 4-4.2" fill="none" stroke="#f07a24" stroke-width="1.3"/></symbol>
</svg>

<!-- INSIDE SPREAD -->
<section class="spread spread--inside">
  <div class="header-band"></div>

  <div class="panel panel--1">
    <div class="panel-title">
      <div class="badge"><svg width="30" height="30" viewBox="0 0 30 30"><circle cx="15" cy="15" r="12" fill="none" stroke="#111" stroke-width="2"/><path d="M8 18 L15 10 L22 18" fill="none" stroke="#111" stroke-width="2"/></svg></div>
      <h2>ROOFING</h2>
    </div>
    <div class="card">
      <div class="photo-row">
        <div class="photo" role="img" aria-label="White flat commercial roof with rooftop units" style="width:161px;height:105px;background:linear-gradient(180deg,#bccada 0%,#e9ecef 55%,#d5d8da 100%)"></div>
        <div class="photo" role="img" aria-label="Workers installing blue metal roof panels" style="width:161px;height:105px;background:linear-gradient(150deg,#2f5f93 0%,#4e86b9 60%,#c7c36a 100%)"></div>
      </div>
      <ul class="ticks">
        <li><svg class="tick"><use href="#tick"/></svg>New Construction</li>
        <li><svg class="tick"><use href="#tick"/></svg>Preventative Maintenance</li>
        <li><svg class="tick"><use href="#tick"/></svg>Tear off and Replacement</li>
        <li><svg class="tick"><use href="#tick"/></svg>Inspections</li>
        <li><svg class="tick"><use href="#tick"/></svg>Vented Full Overlay</li>
      </ul>
      <p class="copy">Our free roof evaluation will offer you insight to determine whether you are in need of a routine maintenance plan or if the roof is due for repairs, vented overlay or a full replacement.</p>
    </div>
    <div class="photo" role="img" aria-label="Aerial view of a large commercial building roof" style="margin-top:14px;height:135px;background:linear-gradient(160deg,#7c8a70 0%,#3c4a5c 45%,#8a8f94 100%)"></div>
    <ul class="ticks ticks--single">
      <li><svg class="tick"><use href="#tick"/></svg><span><b>Flat Roof:</b> EPDM, Modified Bitumen, TPO</span></li>
      <li><svg class="tick"><use href="#tick"/></svg><span><b>Metal Roof:</b> Standing Seam</span></li>
      <li><svg class="tick"><use href="#tick"/></svg><span><b>Shingles:</b> <span class="muted">Standard + Steep Slope Structures</span></span></li>
      <li><svg class="tick"><use href="#tick"/></svg><span><b>Glass</b> Atriums + Skylights</span></li>
      <li><svg class="tick"><use href="#tick"/></svg><span><b>Eco</b> Roofing + Green Roofing</span></li>
    </ul>
  </div>

  <div class="panel panel--2">
    <div class="panel-title">
      <div class="badge"><svg width="30" height="30" viewBox="0 0 30 30"><rect x="7" y="9" width="16" height="14" fill="none" stroke="#111" stroke-width="2"/><path d="M11 9V6h8v3" fill="none" stroke="#111" stroke-width="2"/></svg></div>
      <h2>CONSTRUCTION</h2>
    </div>
    <div class="card">
      <div class="photo" role="img" aria-label="Modern commercial office building with parking lot" style="height:165px;background:linear-gradient(180deg,#b8cde0 0%,#e8e3d6 45%,#3b3d40 100%)"></div>
      <ul class="ticks" style="grid-template-columns:1fr 1fr">
        <li><svg class="tick"><use href="#tick"/></svg>New Construction 5,000sf +</li>
        <li><svg class="tick"><use href="#tick"/></svg>HVAC / Plumbing / Electrical</li>
        <li><svg class="tick"><use href="#tick"/></svg>Full Gut Renovation</li>
        <li><svg class="tick"><use href="#tick"/></svg>Fire Alarm Systems &amp; Testing</li>
        <li><svg class="tick"><use href="#tick"/></svg>Carpentry</li>
        <li><svg class="tick"><use href="#tick"/></svg>City Storm Water</li>
      </ul>
    </div>
    <div class="card" style="margin-top:14px">
      <div class="photo" role="img" aria-label="Red brick commercial building with paved drive" style="height:165px;background:linear-gradient(180deg,#a9c6e3 0%,#a0533d 45%,#3a3a3c 100%)"></div>
      <ul class="ticks" style="grid-template-columns:1fr 1fr">
        <li><svg class="tick"><use href="#tick"/></svg>New Construction 5,000sf +</li>
        <li><svg class="tick"><use href="#tick"/></svg>HVAC / Plumbing / Electrical</li>
        <li><svg class="tick"><use href="#tick"/></svg>Full Gut Renovation</li>
        <li><svg class="tick"><use href="#tick"/></svg>Fire Alarm Systems &amp; Testing</li>
        <li><svg class="tick"><use href="#tick"/></svg>Carpentry</li>
        <li><svg class="tick"><use href="#tick"/></svg>City Storm Water</li>
      </ul>
    </div>
  </div>

  <div class="panel panel--3">
    <div class="panel-title">
      <div class="badge"><svg width="30" height="30" viewBox="0 0 30 30"><circle cx="15" cy="15" r="12" fill="none" stroke="#111" stroke-width="2"/><circle cx="15" cy="15" r="6" fill="none" stroke="#111" stroke-width="2"/></svg></div>
      <h2>RESTORATION</h2>
    </div>
    <div class="photo" role="img" aria-label="Commercial building on fire with heavy black smoke" style="height:175px;background:linear-gradient(170deg,#2b2b2f 0%,#4a4448 40%,#d4572a 62%,#7d8a96 100%)"></div>
    <ul class="ticks">
      <li><svg class="tick"><use href="#tick"/></svg>Fire Restoration</li>
      <li><svg class="tick"><use href="#tick"/></svg>Mold Remediation</li>
      <li><svg class="tick"><use href="#tick"/></svg>Smoke Restoration</li>
      <li><svg class="tick"><use href="#tick"/></svg>Storm Restoration</li>
      <li><svg class="tick"><use href="#tick"/></svg>Flood Restoration</li>
    </ul>
    <div class="photo" role="img" aria-label="Flooded street with water pouring from a building" style="margin-top:28px;height:165px;background:linear-gradient(180deg,#5a5e60 0%,#a9b4b6 50%,#cfd8d8 100%)"></div>
    <p class="copy" style="padding:10px 4px 0">Has your property suffered from a fire or natural disaster? Allow us to pick up the pieces from clean up to rebuild. We work with your insurance company to alleviate the burden by sending an expert team to overcome the damages. It is our priority to restore your property and get you back to business.</p>
  </div>

  <div class="footer-band" role="img" aria-label="City skyline silhouette">
    <span class="url" style="left:0">www.brandtroof.com</span>
    <span class="url" style="left:373.33px">www.brandtroof.com</span>
    <span class="url" style="left:746.66px">www.brandtroof.com</span>
  </div>
</section>

<!-- OUTSIDE SPREAD -->
<section class="spread spread--outside">
  <div class="founder-block"></div>
  <div class="founder-photo" role="img" aria-label="Portrait of the company founder seated in a carved wooden chair"></div>
  <div class="founder">
    <h3>Founder &amp; Priciple</h3>
    <p class="role">Lena Marsh, certified interior designer and builder.</p>
    <p>Brandt Commercial is a woman-owned business serving the roofing and construction industry. With more than 15 years of experience and strategic partnerships it is our goal to share our industry knowledge and expertise to build and maintain the systems that protect your assets. We strive to build quality structures and devise the best roofing solution for your requirements and budget. Clients receive the utmost attention to detail in understanding the work scope and expectations of a project from beginning to end. We are committed to quality installation processes and providing safe work environments for our skilled trades men and women.</p>
  </div>

  <div class="mission">
    <h3>FAITH BASED,<strong>MISSION MINDED</strong></h3>
    <p>10% of all Brandt Commercial proceeds support our mission to restore hope and inspire change into the lives of those who we are all connected.</p>
    <p class="invite">Sign with Brandt Commercial and select one of our sponsored charities:</p>
    <div class="charity">
      <h4>Clear Water Alliance</h4>
      <div class="row">
        <svg width="30" height="30" viewBox="0 0 30 30"><path d="M15 4c4 6 7 10 7 14a7 7 0 0 1-14 0c0-4 3-8 7-14z" fill="none" stroke="#111" stroke-width="1.8"/></svg>
        <div><h5>Clean Water Efforts</h5><p>Bring clean water wells, sanitation, &amp; hygiene to communities in need.</p></div>
      </div>
    </div>
    <div class="charity">
      <h4>Hope Harbor Center</h4>
      <div class="row">
        <svg width="30" height="30" viewBox="0 0 30 30"><circle cx="15" cy="15" r="11" fill="none" stroke="#111" stroke-width="1.8"/><circle cx="15" cy="15" r="5" fill="none" stroke="#111" stroke-width="1.8"/></svg>
        <div><h5>Local and World Missionaries</h5><p>Rebuild and restore, food shortage aid and Christian outreach.</p></div>
      </div>
    </div>
    <div class="charity">
      <h4>Safe Passage Network</h4>
      <div class="row">
        <svg width="30" height="30" viewBox="0 0 30 30"><path d="M9 26V12a2 2 0 0 1 4 0v-5a2 2 0 0 1 4 0v5a2 2 0 0 1 4 0v14z" fill="none" stroke="#111" stroke-width="1.8"/></svg>
        <div><h5>End Child Sex Trafficking</h5><p>Bring an end to sex trafficking through prevention, restoration, and justice.</p></div>
      </div>
    </div>
  </div>

  <div class="contact">
    <svg width="36" height="36" viewBox="0 0 36 36"><circle cx="18" cy="18" r="17" fill="#111"/><path d="M13 10l3 0 1.5 4-2 1.5a9 9 0 0 0 5 5l1.5-2 4 1.5v3a2 2 0 0 1-2 2A15 15 0 0 1 11 12a2 2 0 0 1 2-2z" fill="#fff"/></svg>
    <div class="phone">(312) 555-0148</div>
    <svg width="36" height="36" viewBox="0 0 36 36"><circle cx="18" cy="18" r="17" fill="#111"/><path d="M18 8a6 6 0 0 1 6 6c0 5-6 12-6 12s-6-7-6-12a6 6 0 0 1 6-6z" fill="#fff"/><circle cx="18" cy="14" r="2.2" fill="#111"/></svg>
    <p class="addr">4810 Harlow Street, Suite C<br>Oak Ridge, IL 60400</p>
  </div>

  <svg class="diagonal" width="1120" height="695" viewBox="0 0 1120 695" aria-hidden="true">
    <polygon points="655,0 705,0 935,470 885,470" fill="#0d0d0d"/>
    <polygon points="747,130 1120,130 1120,465 909,465" fill="#0d0d0d"/>
  </svg>
  <svg class="diagonal" width="1120" height="695" viewBox="0 0 1120 695" role="img" aria-label="Roofer in hard hat and safety vest installing slate roof tiles">
    <defs><linearGradient id="roofPhoto" x1="0" y1="0" x2="1" y2="1"><stop offset="0" stop-color="#b9c9d8"/><stop offset=".45" stop-color="#5b6670"/><stop offset=".75" stop-color="#b7d43a"/><stop offset="1" stop-color="#3d4650"/></linearGradient></defs>
    <polygon points="756,138 1120,138 1120,457 913,457" fill="url(#roofPhoto)"/>
  </svg>

  <div class="brand">
    <span class="mark"></span>
    <span class="name">Brandt Commercial Roofing</span>
  </div>

  <div class="values">KNOWLEDGEABLE<br><span class="hl">TRUSTWORTHY</span><br>COMMITTED</div>

  <div class="footer-band" role="img" aria-label="City skyline silhouette">
    <span class="url" style="left:0">www.brandtroof.com</span>
    <span class="url" style="left:373.33px">www.brandtroof.com</span>
    <span class="url" style="left:746.66px">www.brandtroof.com</span>
  </div>
</section>

</body>
</html>
```